Real Estate Webpage Design

We have an existing website: ferndaleestatecollective.com.au
We focus customised service mainly on Property Management and second-hand property sales.
We are not entirely happy about the current design and layout can stay roughly the same as the back end coding is linked to a CRM system.
We would like to see the design are more reachable to our clients and appearing.
Please check our Website Design Draft for more details.

Industry/Entity Type

Real estate Agency

Number of Pages Required

5+ page

Font styles to use
Sans Serif

Colors

Designer to choose colors to be used in the design.

```html
<!DOCTYPE html>
<html lang="en">
<head>
<meta charset="utf-8">
<title>Ferndale Estate Collective – Real Estate</title>
<link rel="stylesheet" href="https://fonts.googleapis.com/css2?family=Lato:ital,wght@0,400;0,700;0,900;1,400&family=Hind:wght@400;600;700&display=swap">
<style>
:root{
  --gold:#e9b437;
  --gold-dark:#d9a22a;
  --ink:#1d1f24;
  --text:#4a4d55;
  --muted:#6d7078;
  --band:#f1f1f1;
  --footer:#2c3544;
  --footer-line:#46505f;
  --white:#ffffff;
}
*{box-sizing:border-box;margin:0;padding:0}
html,body{width:1200px;height:3944px;overflow:hidden}
body{position:relative;background:var(--white);font-family:"Lato",sans-serif;color:var(--text)}
.abs{position:absolute}
h1,h2,h3{font-family:"Hind",sans-serif;color:var(--ink);font-weight:700}
.section-title{position:absolute;left:0;width:1200px;text-align:center;font-size:34px;line-height:1}
.section-sub{position:absolute;left:0;width:1200px;text-align:center;font-size:11.5px;line-height:19px;color:var(--text)}
.btn{position:absolute;background:var(--gold);color:var(--ink);font-weight:700;font-size:12.5px;display:flex;align-items:center;justify-content:center;border-radius:3px}

/* hero */
.hero{left:0;top:0;width:1200px;height:628px;background:linear-gradient(90deg,#23262c 0%,#3a3f45 38%,#5b6453 70%,#6b7a4a 100%)}
.hero-grass{left:480px;top:400px;width:720px;height:228px;background:linear-gradient(180deg,#5d7a36,#486629)}
.hero-pool{left:0;top:500px;width:480px;height:128px;background:linear-gradient(90deg,#2d4b5a,#3e5a66)}
.brand{left:158px;top:48px;display:flex;align-items:center;gap:10px;color:var(--gold);font-weight:900;font-size:32px}
.brand-mark{width:34px;height:34px;background:var(--gold)}
.nav{left:544px;top:60px;display:flex;gap:21px;font-size:12px;color:var(--white)}
.nav .active{color:var(--gold)}
.nav-cta{left:944px;top:52px;width:98px;height:34px}
.hero-title{left:155px;top:188px;font-size:56px;line-height:58px;color:var(--white);font-weight:700}
.hero-title .light{font-weight:400}
.hero-title .gold{color:var(--gold)}
.hero-text{left:155px;top:370px;width:400px;font-size:11.5px;line-height:22px;color:var(--white)}
.hero-cta{left:155px;top:432px;width:165px;height:41px}

/* feature strip */
.strip{left:0;top:628px;width:1200px;height:80px;background:var(--white);border-bottom:1px solid #e5e5e5;display:flex}
.strip-item{height:80px;display:flex;align-items:center;gap:12px;padding-left:42px;font-size:13px;font-weight:700;color:var(--ink);line-height:16px;border-right:1px solid #e5e5e5}
.strip-item.active{background:var(--gold);height:93px;margin-top:-13px;padding-top:13px}
.strip-item svg{width:32px;height:32px;flex:none}

/* properties */
.band-a{left:0;top:1060px;width:1200px;height:571px;background:var(--band)}
.prop{width:210px;height:238px;top:871px}
.prop-label{position:absolute;left:17px;right:17px;bottom:16px;height:31px;background:var(--gold);color:var(--ink);font-size:11.5px;font-weight:700;display:flex;align-items:center;justify-content:center}

/* who */
.who-title{left:155px;top:1190px;font-size:31px}
.who-p{left:155px;width:490px;font-size:11.5px;line-height:22.5px;color:var(--text)}
.promise-title{left:155px;top:1432px;font-size:25px}
.who-photo{left:684px;top:1179px;width:372px;height:370px;background:linear-gradient(160deg,#b9cfdc 0%,#d8cfb8 55%,#a9b79c 100%)}

/* learn */
.learn{top:1811px;height:133px;background:var(--white);box-shadow:0 4px 16px rgba(0,0,0,.07);display:flex;flex-direction:column;align-items:center;font-size:12.5px;font-weight:700;color:var(--ink)}
.learn.active{background:var(--gold)}
.learn-icon{width:64px;height:64px;border-radius:50%;background:#eeeeef;margin-top:20px;margin-bottom:14px;display:flex;align-items:center;justify-content:center}
.learn.active .learn-icon{background:#f1c763}

/* market */
.band-b{left:0;top:2029px;width:1200px;height:405px;background:linear-gradient(180deg,#d9dadd,#c4c6cb)}
.video{left:153px;top:2208px;width:894px;height:387px;background:linear-gradient(180deg,#2a3853 0%,#485a78 40%,#7d7560 70%,#3b4a33 100%)}
.play{left:558px;top:2358px;width:84px;height:84px;border-radius:50%;border:2px solid rgba(255,255,255,.8);display:flex;align-items:center;justify-content:center}
.play span{width:62px;height:62px;border-radius:50%;background:var(--white);display:flex;align-items:center;justify-content:center}
.arrow-btn{width:44px;height:44px;border-radius:50%;display:flex;align-items:center;justify-content:center}

/* testimonial */
.avatar{left:563px;top:2719px;width:74px;height:74px;border-radius:50%;background:linear-gradient(180deg,#e5e5e7,#b9bcc2)}
.quote-mark{left:578px;top:2806px;font-family:"Hind",sans-serif;font-size:80px;line-height:1;color:#d5d5d7;font-weight:700}
.quote{left:150px;top:2834px;width:900px;text-align:center;font-style:italic;font-size:12.5px;line-height:28.5px;color:var(--ink)}
.client{left:0;top:2934px;width:1200px;text-align:center;font-size:17px;color:var(--ink)}
.stars{left:543px;top:2961px;display:flex;gap:7px}

/* articles */
.feature-article{left:155px;top:3105px;width:430px;height:331px;background:linear-gradient(180deg,#8b9ab3 0%,#b8a88e 45%,#2c3442 70%,#1a2029 100%)}
.feature-caption{position:absolute;left:14px;bottom:18px;width:290px;font-size:14px;line-height:17px;font-weight:700;color:var(--white)}
.feature-date{position:absolute;right:14px;bottom:58px;font-size:9px;color:var(--white);letter-spacing:.5px}
.feature-more{position:absolute;right:14px;bottom:26px;font-size:11px;color:var(--gold);text-decoration:underline}
.art-img{left:602px;width:131px;height:99px}
.art-body{left:743px;width:300px}
.art-title{font-size:13px;line-height:17px;font-weight:700;color:var(--ink)}
.art-text{font-size:9.5px;line-height:14.5px;color:var(--muted);margin-top:3px}
.art-more{font-size:11px;color:var(--ink);text-decoration:underline;margin-top:6px}
.all-btn{left:527px;top:3463px;width:147px;height:41px}

/* footer */
.footer{left:0;top:3576px;width:1200px;height:368px;background:var(--footer);color:#d7dbe2}
.f-head{position:absolute;top:57px;font-size:17px;font-weight:700;color:var(--white);font-family:"Hind",sans-serif}
.f-links{position:absolute;left:161px;top:97px;font-size:11.5px;line-height:28px;color:#d7dbe2}
.f-row{position:absolute;display:flex;gap:10px;font-size:11.5px;line-height:16px}
.f-row svg{flex:none;margin-top:2px}
.social{position:absolute;left:590px;top:190px;display:flex;gap:9px}
.social span{width:20px;height:20px;border-radius:50%;background:var(--white)}
.f-news{position:absolute;left:778px;top:97px;width:270px;font-size:11.5px;line-height:20px}
.f-input{position:absolute;left:782px;top:158px;width:262px;height:40px;background:var(--white);border-radius:3px;font-size:11.5px;color:#333;padding-left:16px;display:flex;align-items:center}
.f-btn{left:782px;top:214px;width:262px;height:40px}
.f-bottom{position:absolute;left:0;top:313px;width:1200px;border-top:1px solid var(--footer-line)}
.copyright{position:absolute;left:158px;top:331px;font-size:10px;color:#d7dbe2}
.legal{position:absolute;right:157px;top:331px;font-size:10px;color:#d7dbe2}
</style>
</head>
<body>

<!-- hero -->
<section class="abs hero" role="img" aria-label="Modern house with outdoor lounge on a wooden deck beside a lawn and pool at dusk"></section>
<div class="abs hero-grass" role="img" aria-label="Garden lawn"></div>
<div class="abs hero-pool" role="img" aria-label="Pool water"></div>
<div class="abs brand"><span class="brand-mark"></span>Ferndale</div>
<nav class="abs nav">
  <span class="active">Home</span><span>About Us</span><span>Leasing ▾</span><span>Buy</span><span>Sell ▾</span><span>Our Team</span><span>Blog</span>
</nav>
<div class="btn nav-cta">Contact Us</div>
<h1 class="abs hero-title">Ferndale -<br><span class="light">Rooted in </span><span class="gold">The<br>Home</span></h1>
<p class="abs hero-text">Ferndale is about "the home, the house", buying a property is one of the most expensive expenses and important assets for people.</p>
<div class="btn hero-cta">Explore Property</div>

<div class="abs strip">
  <div class="strip-item" style="width:219px">
    <svg viewBox="0 0 32 32" fill="none" stroke="#1d1f24" stroke-width="1.6"><rect x="4" y="8" width="14" height="20"/><rect x="18" y="14" width="10" height="14"/><path d="M8 13h6M8 18h6M8 23h6M21 19h4M21 23h4"/></svg>
    Australia Off Plan<br>Property</div>
  <div class="strip-item active" style="width:234px">
    <svg viewBox="0 0 32 32" fill="none" stroke="#1d1f24" stroke-width="1.6"><rect x="6" y="6" width="20" height="22"/><path d="M10 11h4M18 11h4M10 16h4M18 16h4M10 21h4M18 21h4M3 28h26"/></svg>
    Australia New Build<br>Property</div>
  <div class="strip-item" style="width:231px">
    <svg viewBox="0 0 32 32" fill="none" stroke="#1d1f24" stroke-width="1.6"><circle cx="20" cy="20" r="8"/><path d="M20 16v8M4 28V14l8-6 8 6"/></svg>
    Highly Growth Net<br>Worth</div>
  <div class="strip-item" style="width:265px">
    <svg viewBox="0 0 32 32" fill="none" stroke="#1d1f24" stroke-width="1.6"><circle cx="16" cy="9" r="5"/><path d="M6 28c0-6 4-10 10-10s10 4 10 10z"/><circle cx="16" cy="23" r="3"/></svg>
    Development in Property<br>Funding</div>
  <div class="strip-item" style="width:251px;border-right:none">
    <svg viewBox="0 0 32 32" fill="none" stroke="#1d1f24" stroke-width="1.6"><path d="M4 28h24M7 28v-6M13 28v-10M19 28v-14M25 28v-18M6 16l8-6 5 3 8-7"/></svg>
    High Growth in<br>Property Management</div>
</div>

<!-- properties -->
<div class="abs band-a"></div>
<h2 class="section-title" style="top:773px">Check Out Our Properties</h2>
<p class="section-sub" style="top:813px">Helping landlords and vendor alike to complete efficient property transactions is our signature talent.<br>Our poise, precision, and insight give us an unparalleled advantage.</p>
<div class="abs prop" style="left:153px;background:linear-gradient(180deg,#a9cde6,#8a7a5e 60%,#2f3440)" role="img" aria-label="Apartment towers under a blue sky"><div class="prop-label">Property for Lease</div></div>
<div class="abs prop" style="left:380px;background:linear-gradient(180deg,#c7d9ea,#7b8794 50%,#3c4350)" role="img" aria-label="Suburban family house with a double garage"><div class="prop-label">Tenant Form</div></div>
<div class="abs prop" style="left:609px;background:linear-gradient(180deg,#c9dcea,#b8b6ae 50%,#444a52)" role="img" aria-label="Modern commercial apartment blocks"><div class="prop-label">Commercial for Lease</div></div>
<div class="abs prop" style="left:836px;background:linear-gradient(180deg,#eceef2,#c3c7cf 55%,#3d434c)" role="img" aria-label="Small model house on a pale background"><div class="prop-label">Leased Appriasal</div></div>

<!-- who -->
<h2 class="abs who-title">Who is Ferndale?</h2>
<p class="abs who-p" style="top:1243px">Ferndale is about "the home, the house", buying a property is one of the most expensive expenses and important assets for people. Ferndale is a real estate company located in Ferndale, Canberra.</p>
<p class="abs who-p" style="top:1322px">Being a portfolio sales agent and property manager, coupled with our high–profile international real estate experience, Ferndale is considered a market leader on the cutting edge with deep industry knowledge, ranging from landlord–tenant relationships, residential purchases.</p>
<h3 class="abs promise-title">Our Promise</h3>
<p class="abs who-p" style="top:1468px;width:510px">Ferndale Estate Collective aims to at all times maintain the utmost levels of service for our customers and strives to place itself at the forefront of Property Management Services within the Real Estate industry.</p>
<div class="abs who-photo" role="img" aria-label="Photo collage of apartment buildings and gardens"></div>

<!-- learn -->
<h2 class="section-title" style="top:1704px">Learn About Property</h2>
<p class="section-sub" style="top:1748px">We are here to guide you into your dream property and will always enjoy being part of your first step<br>to completing that project you've always dreamed of.</p>
<div class="abs learn" style="left:156px;width:164px"><div class="learn-icon"><svg width="30" height="30" viewBox="0 0 30 30" fill="none" stroke="#555" stroke-width="1.5"><rect x="6" y="4" width="18" height="22"/><path d="M10 10h10M10 15h10M10 20h6"/></svg></div>Australia Property Tax</div>
<div class="abs learn" style="left:337px;width:165px"><div class="learn-icon"><svg width="30" height="30" viewBox="0 0 30 30" fill="none" stroke="#555" stroke-width="1.5"><rect x="5" y="6" width="20" height="14" rx="2"/><path d="M10 24h10M15 20v4M11 13l3 3 5-6"/></svg></div>Spot a Online Scam</div>
<div class="abs learn active" style="left:516px;width:167px"><div class="learn-icon"><svg width="30" height="30" viewBox="0 0 30 30" fill="none" stroke="#555" stroke-width="1.5"><rect x="6" y="8" width="18" height="18"/><path d="M10 13h4M16 13h4M10 18h4M16 18h4M4 26h22M10 8V4h10v4"/></svg></div>Free Mini Series</div>
<div class="abs learn" style="left:697px;width:165px"><div class="learn-icon"><svg width="30" height="30" viewBox="0 0 30 30" fill="none" stroke="#555" stroke-width="1.5"><rect x="5" y="10" width="9" height="16"/><rect x="14" y="5" width="11" height="21"/><path d="M17 10h5M17 15h5M17 20h5M8 15h3M8 20h3"/></svg></div>New Building/Off Plan</div>
<div class="abs learn" style="left:877px;width:164px"><div class="learn-icon"><svg width="30" height="30" viewBox="0 0 30 30" fill="none" stroke="#555" stroke-width="1.5"><path d="M3 14l6-4 6 4 6-4 6 4M9 12l6 6 4-3M5 15l7 6"/></svg></div>Our Group Promise</div>

<!-- market -->
<div class="abs band-b" role="img" aria-label="Faded grey city skyline"></div>
<h2 class="section-title" style="top:2099px">Property Market Prediction Rants</h2>
<p class="section-sub" style="top:2148px">Since we connect people to their homes and to their communities. Relationships are everything<br>to us. Our clients' needs and best interests are at the heart of everything we do.</p>
<div class="abs video" role="img" aria-label="Modern single storey home with palm trees lit at dusk"></div>
<div class="abs play"><span><svg width="16" height="20" viewBox="0 0 16 20"><rect x="2" y="1" width="4" height="18" fill="#1d1f24"/><rect x="10" y="1" width="4" height="18" fill="#1d1f24"/></svg></span></div>
<div class="abs arrow-btn" style="left:99px;top:2415px;background:var(--gold)"><svg width="20" height="14" viewBox="0 0 20 14" fill="none" stroke="#fff" stroke-width="2"><path d="M19 7H2M8 1L2 7l6 6"/></svg></div>
<div class="abs arrow-btn" style="left:1054px;top:2415px;background:#111"><svg width="20" height="14" viewBox="0 0 20 14" fill="none" stroke="#fff" stroke-width="2"><path d="M1 7h17M12 1l6 6-6 6"/></svg></div>

<!-- testimonial -->
<h2 class="section-title" style="top:2663px">What Our Client Says</h2>
<div class="abs avatar" role="img" aria-label="Client portrait"></div>
<div class="abs quote-mark">“</div>
<p class="abs quote">They are a greatly professional, organized and experienced team with extensive knowledge and understanding of the local market. My husband and I were provided with excellent feedback in a simple language we could understand and advice throughout the house journey and we were very pleased with the results. We highly recommend Ferndale Estate Collective to anyone buying, selling or In need of property management in the local area.</p>
<svg class="abs" style="left:92px;top:2866px" width="28" height="18" viewBox="0 0 28 18" fill="none" stroke="#999" stroke-width="2.5"><path d="M27 9H3M10 2L3 9l7 7"/></svg>
<svg class="abs" style="left:1081px;top:2866px" width="28" height="18" viewBox="0 0 28 18" fill="none" stroke="#999" stroke-width="2.5"><path d="M1 9h24M18 2l7 7-7 7"/></svg>
<div class="abs client">Clara Joan Mercer</div>
<div class="abs stars">
  <svg width="18" height="18" viewBox="0 0 20 20"><path d="M10 1l2.8 6 6.2.7-4.7 4.3 1.3 6.3L10 15l-5.6 3.3 1.3-6.3L1 7.7 7.2 7z" fill="var(--gold)"/></svg>
  <svg width="18" height="18" viewBox="0 0 20 20"><path d="M10 1l2.8 6 6.2.7-4.7 4.3 1.3 6.3L10 15l-5.6 3.3 1.3-6.3L1 7.7 7.2 7z" fill="var(--gold)"/></svg>
  <svg width="18" height="18" viewBox="0 0 20 20"><path d="M10 1l2.8 6 6.2.7-4.7 4.3 1.3 6.3L10 15l-5.6 3.3 1.3-6.3L1 7.7 7.2 7z" fill="var(--gold)"/></svg>
  <svg width="18" height="18" viewBox="0 0 20 20"><path d="M10 1l2.8 6 6.2.7-4.7 4.3 1.3 6.3L10 15l-5.6 3.3 1.3-6.3L1 7.7 7.2 7z" fill="var(--gold)"/></svg>
  <svg width="18" height="18" viewBox="0 0 20 20"><path d="M10 1l2.8 6 6.2.7-4.7 4.3 1.3 6.3L10 15l-5.6 3.3 1.3-6.3L1 7.7 7.2 7z" fill="var(--gold)"/></svg>
</div>

<!-- articles -->
<h2 class="section-title" style="top:3046px">Our Latest Articles</h2>
<article class="abs feature-article" role="img" aria-label="City towers reflected in a river at dusk">
  <div class="feature-date">SEPTEMBER 10, 2021</div>
  <div class="feature-caption">2021 Sees Demand Surge in Manchester Property Management Surge for Buy-to-Let Properties</div>
  <div class="feature-more">Learn More ⟶</div>
</article>
<div class="abs art-img" style="top:3105px;background:linear-gradient(180deg,#c9b9a6,#8a6e57 55%,#4b3d35)" role="img" aria-label="City skyline across a river"></div>
<div class="abs art-body" style="top:3103px"><div class="art-title">Off Plan Property Management in Trafford Manchester</div><div class="art-text">Off Plan Property Investment in Trafford. An Off Plan Property Investment in Trafford is an excellent way to invest in...</div><div class="art-more">Learn More ⟶</div></div>
<div class="abs art-img" style="top:3221px;background:linear-gradient(180deg,#5b96d6,#9bbbd8 50%,#3f6a8a)" role="img" aria-label="Waterfront towers under a blue sky"></div>
<div class="abs art-body" style="top:3219px"><div class="art-title">Kent Property Management: Where Houses Have Been Selling Like Hot Cakes This Year</div><div class="art-text">With its scenic nature, rolling hills and mesmerising coastline, paired up with a contemporary and bustling town centre, Kent...</div><div class="art-more">Learn More ⟶</div></div>
<div class="abs art-img" style="top:3337px;background:linear-gradient(180deg,#9cc2e4,#d5d9de 45%,#5b6a78)" role="img" aria-label="White apartment buildings"></div>
<div class="abs art-body" style="top:3335px"><div class="art-title">Manchester Transport Links Is Using AI Technology to Augment Traffic and City Safety</div><div class="art-text">The regional transit authority, in partnership with a city sensor lab, and their rollout of new technology is set to...</div><div class="art-more">Learn More ⟶</div></div>
<div class="btn all-btn">View All Articles</div>

<!-- footer -->
<footer class="abs footer">
  <div class="f-head" style="left:158px">Navigate</div>
  <div class="f-links">Home<br>About Us<br>Leasing<br>Buy<br>Sell<br>Our Team<br>Blog</div>
  <div class="f-head" style="left:295px">Contact us</div>
  <div class="f-row" style="left:295px;top:97px"><svg width="12" height="15" viewBox="0 0 12 15"><path d="M6 0a6 6 0 0 1 6 6c0 4-6 9-6 9S0 10 0 6a6 6 0 0 1 6-6z" fill="var(--gold)"/><circle cx="6" cy="6" r="2.2" fill="var(--footer)"/></svg><span>18/4 Wattle Grove Rd, Ferndale,<br>ACT, 2915</span></div>
  <div class="f-row" style="left:295px;top:137px"><svg width="13" height="13" viewBox="0 0 13 13"><path d="M3 0l2 3-1.3 1.6a8 8 0 0 0 4.7 4.7L10 8l3 2-1.5 3C5 13 0 8 0 1.5z" fill="var(--gold)"/></svg><span>02 6000 1234</span></div>
  <div class="f-row" style="left:295px;top:168px"><svg width="13" height="13" viewBox="0 0 13 13"><rect x="0" y="3" width="13" height="10" fill="var(--gold)"/><rect x="3" y="0" width="7" height="4" fill="var(--gold)"/></svg><span>2 6000 5678</span></div>
  <div class="f-head" style="left:565px">Trading hours</div>
  <div class="f-row" style="left:565px;top:97px"><svg width="13" height="13" viewBox="0 0 13 13"><rect width="13" height="13" rx="2" fill="var(--gold)"/><circle cx="6.5" cy="7" r="3" fill="var(--footer)"/></svg><span>Monday – Friday<br>8:30 am – 5:00pm</span></div>
  <div class="f-row" style="left:565px;top:140px"><svg width="13" height="13" viewBox="0 0 13 13"><rect width="13" height="13" rx="2" fill="var(--gold)"/><circle cx="6.5" cy="7" r="3" fill="var(--footer)"/></svg><span>Weekend – Closed<br>Public holiday – Closed</span></div>
  <div class="social"><span></span><span></span><span></span></div>
  <div class="f-head" style="left:778px">Our Newsletter</div>
  <p class="f-news">Get regular updates about Ferndale Estate case studies and upcoming events.</p>
  <div class="f-input">Email Address...</div>
  <div class="btn f-btn">View All Articles</div>
  <div class="f-bottom"></div>
  <div class="copyright">Copyright 2022 Ferndale Estate Collective. All Rights Reserved.</div>
  <div class="legal">Terms &amp; Conditions &nbsp;&nbsp;|&nbsp;&nbsp; Privacy Policy</div>
</footer>

</body>
</html>
```